Construction business card

I need a new business card, they can connect with my logo, brand.
What we do is residential house , design and build
I like: Navy blue / black
I attached our logo, brand,
and, some idea for business card.

```html
<!DOCTYPE html>
<html lang="en">
<head>
<meta charset="utf-8">
<title>Harlow Building Group – Business Card</title>
<link href="https://fonts.googleapis.com/css2?family=Poppins:wght@400;700&display=swap" rel="stylesheet">
<style>
  :root {
    --backdrop: #b1b2b1;
    --card-blue: #307bc2;
    --card-blue-deep: #2a6eae;
    --ink-white: #ffffff;
    --shadow: rgba(0, 0, 0, 0.28);
  }
  * { box-sizing: border-box; margin: 0; padding: 0; }
  html, body {
    width: 1200px;
    height: 939px;
    overflow: hidden;
    background: var(--backdrop);
    font-family: "Poppins", sans-serif;
  }
  .canvas {
    position: relative;
    width: 1200px;
    height: 939px;
  }
  .card {
    position: absolute;
    width: 520px;
    height: 317px;
    background: var(--card-blue);
    box-shadow: 0 10px 24px var(--shadow);
    color: var(--ink-white);
  }
  .card--front { left: 110px; top: 110px; }
  .card--back { left: 570px; top: 500px; }

  .brand-mark {
    position: absolute;
    inset: 0;
    display: flex;
    align-items: center;
    justify-content: center;
    gap: 14px;
  }
  .brand-mark__square {
    width: 26px;
    height: 26px;
    background: var(--ink-white);
  }
  .brand-mark__name {
    font-weight: 700;
    font-size: 30px;
    letter-spacing: 0.5px;
    text-transform: uppercase;
    color: var(--ink-white);
  }

  .brand-faint {
    position: absolute;
    right: 26px;
    top: 74px;
    font-weight: 700;
    font-size: 22px;
    text-transform: uppercase;
    color: var(--card-blue-deep);
    text-align: right;
    line-height: 1.1;
  }

  .contact {
    position: absolute;
    left: 34px;
    bottom: 30px;
  }
  .contact__name {
    font-weight: 700;
    font-size: 22px;
    letter-spacing: 0.5px;
    text-transform: uppercase;
    line-height: 1.1;
  }
  .contact__role {
    font-size: 15px;
    margin-top: 2px;
  }
  .contact__line {
    font-size: 12px;
    line-height: 1.6;
  }
  .contact__company { margin-top: 4px; }
  .contact__list { list-style: none; margin-top: 2px; }
  .contact__item {
    display: flex;
    align-items: center;
    gap: 8px;
    font-size: 12.5px;
    line-height: 1.75;
  }
  .contact__icon { width: 13px; height: 13px; flex: none; }
</style>
</head>
<body>
<main class="canvas">

  <section class="card card--front" aria-label="Business card front">
    <div class="brand-mark">
      <span class="brand-mark__square"></span>
      <span class="brand-mark__name">Harlow Building Group</span>
    </div>
  </section>

  <section class="card card--back" aria-label="Business card back">
    <div class="brand-faint">Harlow<br>Building Group</div>

    <div class="contact">
      <p class="contact__name">Daniel Reyes</p>
      <p class="contact__role">Director</p>
      <p class="contact__line contact__company">HARLOW BUILDING GROUP PTY LTD</p>
      <p class="contact__line">ABN: 48 302 915 667</p>
      <ul class="contact__list">
        <li class="contact__item">
          <svg class="contact__icon" viewBox="0 0 16 16" aria-hidden="true"><rect x="4" y="1" width="8" height="14" rx="1.5" fill="none" stroke="#fff" stroke-width="1.6"/><rect x="6" y="3" width="4" height="8" fill="#fff"/></svg>
          0400 555 012
        </li>
        <li class="contact__item">
          <svg class="contact__icon" viewBox="0 0 16 16" aria-hidden="true"><rect x="1" y="3" width="14" height="10" fill="#fff"/><path d="M1 3 L8 9 L15 3" fill="none" stroke="#307bc2" stroke-width="1.5"/></svg>
          info@harlowbuilding.com.au
        </li>
        <li class="contact__item">
          <svg class="contact__icon" viewBox="0 0 16 16" aria-hidden="true"><path d="M8 15 C8 15 2.5 9 2.5 6 A5.5 5.5 0 0 1 13.5 6 C13.5 9 8 15 8 15 Z" fill="#fff"/><circle cx="8" cy="6" r="2" fill="#307bc2"/></svg>
          48 Maple Grove Rd, Eastwood, VIC 3000
        </li>
        <li class="contact__item">
          <svg class="contact__icon" viewBox="0 0 16 16" aria-hidden="true"><circle cx="8" cy="8" r="6.5" fill="none" stroke="#fff" stroke-width="1.3"/><ellipse cx="8" cy="8" rx="2.8" ry="6.5" fill="none" stroke="#fff" stroke-width="1.1"/><path d="M1.5 8 H14.5 M2.5 5 H13.5 M2.5 11 H13.5" stroke="#fff" stroke-width="1"/></svg>
          www.harlowbuilding.com.au
        </li>
      </ul>
    </div>
  </section>

</main>
</body>
</html>
```